Business Card for Vorla Parts Wholesale supplier

Hi There! I need a new business card for our company. We are specialized in selling Vorla parts, mostly we sell new LCD screens for Zelnar and Drelks. I would like to see that back in the design.

You can find the colors and logo's on our website: www.hartuvo.nl

Industry/Entity Type

Business

Contact Information for Business Card

My Details:
Tobias Lindqvist

Phone: 0031687203316
E-mail: Tobias@hartuvo.nl

Slogan: "Because Quality Matters"

Font styles to use
Sans Serif

Colors

Designer to choose colors to be used in the design.

Requirements
Must have
• A Black backside with the Hartuvo logo on it. The front side should be clean with only my contact details.
• But I'm also open for something really different or awesome!
Nice to have
• Remember that we are in the parts & repairing industry, So i'll be handing those business cards mainly to repair companies. Maybe you can do something with that thought :)

```html
<!DOCTYPE html>
<html lang="en">
<head>
<meta charset="utf-8">
<title>Hartuvo Business Card</title>
<link rel="stylesheet" href="https://fonts.googleapis.com/css2?family=Exo+2:wght@400;600;700&family=PT+Sans:wght@700&display=swap">
<style>
  :root {
    --backdrop: #e9e6e2;
    --card-white: #ffffff;
    --card-black: #000000;
    --brand-orange: #f07323;
    --ink-dark: #1d1d1d;
    --ink-grey: #5a5a5a;
    --slogan-white: #ffffff;
  }
  * { margin: 0; padding: 0; box-sizing: border-box; }
  html, body {
    width: 1200px;
    height: 987px;
    overflow: hidden;
    background: var(--backdrop);
  }
  .canvas {
    position: relative;
    width: 1200px;
    height: 987px;
  }
  .card {
    position: absolute;
    left: 293px;
    width: 615px;
    height: 350px;
    box-shadow: 0 3px 10px rgba(0,0,0,0.18);
    overflow: hidden;
  }
  .card--front { top: 130px; background: var(--card-white); }
  .card--back  { top: 506px; background: var(--card-black); }

  .brand-name {
    position: absolute;
    left: 52px;
    top: 62px;
    display: flex;
    align-items: center;
    gap: 12px;
    font-family: "Exo 2", sans-serif;
    font-weight: 600;
    font-size: 46px;
    color: var(--ink-dark);
    letter-spacing: 0.5px;
  }
  .brand-dot {
    width: 36px;
    height: 36px;
    border-radius: 50%;
    background: var(--brand-orange);
  }

  .contact-list {
    position: absolute;
    left: 52px;
    top: 228px;
    list-style: none;
    font-family: "Exo 2", sans-serif;
    font-size: 16px;
    color: var(--ink-grey);
  }
  .contact-list li {
    display: flex;
    align-items: center;
    gap: 8px;
    height: 24px;
  }
  .contact-icon { width: 14px; height: 14px; flex: none; }

  .holder-name {
    position: absolute;
    right: 52px;
    top: 244px;
    font-family: "Exo 2", sans-serif;
    font-weight: 700;
    font-size: 24px;
    color: var(--brand-orange);
    letter-spacing: 0.5px;
  }
  .edge-tab {
    position: absolute;
    right: 0;
    top: 245px;
    width: 11px;
    height: 36px;
    background: var(--brand-orange);
  }

  .back-brand {
    position: absolute;
    left: 0;
    right: 0;
    top: 136px;
    text-align: center;
    font-family: "Exo 2", sans-serif;
    font-weight: 600;
    font-size: 48px;
    color: var(--brand-orange);
  }
  .slogan {
    position: absolute;
    left: 0;
    right: 0;
    top: 278px;
    text-align: center;
    font-family: "PT Sans", sans-serif;
    font-weight: 700;
    font-size: 20px;
    color: var(--slogan-white);
  }
</style>
</head>
<body>
<main class="canvas">
  <section class="card card--front" aria-label="Card front">
    <div class="brand-name"><span class="brand-dot"></span>Hartuvo</div>

    <ul class="contact-list">
      <li>
        <svg class="contact-icon" viewBox="0 0 24 24" aria-hidden="true">
          <path fill="#f07323" d="M6.6 10.8a15.1 15.1 0 0 0 6.6 6.6l2.2-2.2a1 1 0 0 1 1-.25 11.4 11.4 0 0 0 3.6.57 1 1 0 0 1 1 1V20a1 1 0 0 1-1 1A17 17 0 0 1 3 4a1 1 0 0 1 1-1h3.5a1 1 0 0 1 1 1c0 1.25.2 2.45.57 3.57a1 1 0 0 1-.25 1z"/>
        </svg>
        0031687203316
      </li>
      <li>
        <svg class="contact-icon" viewBox="0 0 24 24" aria-hidden="true">
          <rect x="2" y="5" width="20" height="14" rx="1" fill="#f07323"/>
          <path d="M2 6l10 7 10-7" fill="none" stroke="#ffffff" stroke-width="1.6"/>
        </svg>
        Tobias@hartuvo.nl
      </li>
      <li>
        <svg class="contact-icon" viewBox="0 0 24 24" aria-hidden="true">
          <circle cx="12" cy="12" r="10" fill="#f07323"/>
          <path d="M2 12h20M12 2c3 3 3 17 0 20M12 2c-3 3-3 17 0 20" fill="none" stroke="#ffffff" stroke-width="1.4"/>
        </svg>
        www.hartuvo.nl
      </li>
    </ul>

    <div class="holder-name">Tobias Lindqvist</div>
    <div class="edge-tab"></div>
  </section>

  <section class="card card--back" aria-label="Card back">
    <div class="back-brand">Hartuvo</div>
    <p class="slogan">Because Quality Matters</p>
  </section>
</main>
</body>
</html>
```